brqnal new business card design project

we need a new business card design. you can view info about us @ brqnal-example.com. i have attached an example of our previous card with our previous name that we no longer use. We really liked the design, colors etc. look below to see more info about this project. it asks for a limited number of words. please see our website for more info about our compnay.

Target Market(s)

law enforcement

Contact Information for Business Card

i have uploaded an example of what we used before that we liked.

Font styles to use
Serif

```html
<!DOCTYPE html>
<html lang="en">
<head>
<meta charset="utf-8">
<title>BRQNAL Business Card</title>
<link rel="stylesheet" href="https://fonts.googleapis.com/css2?family=Raleway:wght@200;400&family=Exo+2:wght@500&family=Roboto:ital,wght@0,400;1,400&display=swap">
<style>
  :root {
    --page-bg: #e9e7e4;
    --card-bg: #f3f2f0;
    --band-navy: #0f2238;
    --band-navy-deep: #081727;
    --edge-blue: #1f7fc4;
    --logo-white: #f2f4f6;
    --tag-light: #d7dde3;
    --ink: #1c1f24;
    --ink-soft: #33373d;
    --icon-teal: #1f6f8b;
  }
  * { margin: 0; padding: 0; box-sizing: border-box; }
  html, body {
    width: 1200px;
    height: 1054px;
    overflow: hidden;
    background: var(--page-bg);
  }
  .canvas {
    position: relative;
    width: 1200px;
    height: 1054px;
  }
  .business-card {
    position: absolute;
    left: 100px;
    top: 225px;
    width: 1000px;
    height: 604px;
    background: var(--card-bg);
    border: 1px solid #cfcdc9;
    overflow: hidden;
    box-shadow: 0 10px 30px rgba(0,0,0,0.12);
  }
  .header-band {
    position: absolute;
    left: 0;
    top: 0;
    width: 1000px;
    height: 340px;
  }
  .brand-name {
    position: absolute;
    left: 0;
    width: 100%;
    top: 76px;
    text-align: center;
    font-family: "Raleway", sans-serif;
    font-weight: 200;
    font-size: 90px;
    letter-spacing: 4px;
    line-height: 1;
    color: var(--logo-white);
  }
  .tagline {
    position: absolute;
    left: 0;
    width: 100%;
    top: 187px;
    text-align: center;
    font-family: "Raleway", sans-serif;
    font-weight: 400;
    font-size: 24px;
    letter-spacing: 2.5px;
    line-height: 1;
    color: var(--tag-light);
  }
  .person {
    position: absolute;
    right: 540px;
    top: 392px;
    text-align: right;
  }
  .person-name {
    font-family: "Exo 2", sans-serif;
    font-weight: 500;
    font-size: 40px;
    color: var(--ink);
    line-height: 1.1;
  }
  .person-title {
    margin-top: 10px;
    font-family: "Roboto", sans-serif;
    font-style: italic;
    font-size: 24px;
    color: var(--ink-soft);
  }
  .contact-list {
    position: absolute;
    left: 522px;
    top: 384px;
    list-style: none;
  }
  .contact-item {
    display: flex;
    align-items: center;
    height: 36px;
    font-family: "Roboto", sans-serif;
    font-size: 24px;
    color: var(--ink-soft);
  }
  .contact-icon {
    width: 22px;
    height: 22px;
    margin-right: 22px;
    flex: none;
  }
  .address {
    position: absolute;
    left: 0;
    width: 100%;
    top: 526px;
    text-align: center;
    font-family: "Roboto", sans-serif;
    font-size: 24px;
    color: var(--ink-soft);
  }
</style>
</head>
<body>
<div class="canvas">
  <div class="business-card">
    <svg class="header-band" viewBox="0 0 1000 340" aria-hidden="true">
      <defs>
        <linearGradient id="navyFill" x1="0" y1="0" x2="0" y2="1">
          <stop offset="0" stop-color="#0f2238"/>
          <stop offset="1" stop-color="#081727"/>
        </linearGradient>
      </defs>
      <path d="M0 0 H1000 V235 Q500 410 0 235 Z" fill="url(#navyFill)"/>
      <path d="M0 235 Q500 410 1000 235" fill="none" stroke="var(--edge-blue)" stroke-width="5"/>
    </svg>

    <div class="brand-name">BRQNAL</div>
    <div class="tagline">Trusted Tools for Public Safety</div>

    <div class="person">
      <div class="person-name">Daniel Harrow</div>
      <div class="person-title">Founder/Chief Exe. Officer</div>
    </div>

    <ul class="contact-list">
      <li class="contact-item">
        <svg class="contact-icon" viewBox="0 0 24 24" aria-hidden="true">
          <path d="M3 9 Q12 3 21 9 L19 12 L15 10 L15 8 Q12 7 9 8 L9 10 L5 12 Z" fill="var(--icon-teal)"/>
          <rect x="6" y="13" width="12" height="8" rx="1.5" fill="var(--icon-teal)"/>
        </svg>
        555.010.4821
      </li>
      <li class="contact-item">
        <svg class="contact-icon" viewBox="0 0 24 24" aria-hidden="true">
          <rect x="2" y="5" width="20" height="14" fill="var(--icon-teal)"/>
          <path d="M2 5 L12 13 L22 5" fill="none" stroke="#f3f2f0" stroke-width="1.6"/>
        </svg>
        info@brqnal-example.com
      </li>
      <li class="contact-item">
        <svg class="contact-icon" viewBox="0 0 24 24" aria-hidden="true">
          <circle cx="12" cy="12" r="10" fill="var(--icon-teal)"/>
          <path d="M2 12 H22 M12 2 V22 M12 2 Q5 12 12 22 M12 2 Q19 12 12 22" fill="none" stroke="#f3f2f0" stroke-width="1.2"/>
        </svg>
        www.brqnal-example.com
      </li>
    </ul>

    <div class="address">4120 Larkspur Avenue Dallas, TX 75204</div>
  </div>
</div>
</body>
</html>
```